Furniture & Lighting Wholesaler Needs a Product Catalogue/Look Book

Our company, Vostre Merchant Co, imports quality hand-made furniture, lighting and decor from South Africa. Our products are well-designed and are designed to be used in up-market hotels and homes. Our primary customers are small- to medium-size retail shops.
We require a +/- 14-16 page look book (concept as per attached image) that will be used both in hard-copy and online. We have all of the necessary high-res images, descriptions/text etc. We need you to propose several design concepts from which we can choose, and then execute the design.
Please visit our website www.vostremerchant.example to see the products and their descriptions, as well as to get a feel for our style. Thank you for looking at our project!
Target Market(s)
Boutique Furniture Stores; Interior Designers
Industry/Entity Type
It Company
Font styles to use
Other font styles liked:
- Bauer Bodini and Open Sans Condensed
Look and feel
Each slider illustrates characteristics of the customer's brand and the style your logo design should communicate.

```html
<!DOCTYPE html>
<html lang="en">
<head>
<meta charset="utf-8">
<title>Vostre Merchant Co – Look Book Pages</title>
<link href="https://fonts.googleapis.com/css2?family=Open+Sans:wght@300;400;600&family=Montserrat:wght@600;700&display=swap" rel="stylesheet">
<style>
  :root {
    --bg: #e6e6e6;
    --paper: #ffffff;
    --gold: #b3a57a;
    --gold-soft: #c4b78f;
    --gold-text: #a8996a;
    --ink: #2b2b2b;
    --charcoal: #303030;
    --charcoal-light: #4a4a4a;
    --silver: #e9e9e9;
    --slate: #505255;
    --footer: #dcdcdc;
  }
  * { box-sizing: border-box; margin: 0; padding: 0; }
  html, body { width: 1200px; height: 900px; overflow: hidden; }
  body {
    background: var(--bg);
    font-family: "Open Sans", Arial, sans-serif;
    position: relative;
  }
  .page {
    position: absolute;
    width: 560px;
    height: 400px;
    top: 250px;
    overflow: hidden;
    box-shadow: 0 4px 14px rgba(0,0,0,0.12);
  }

  /* ABOUT US spread page */
  .about-page { left: 610px; background: var(--paper); }
  .about-title {
    position: absolute; left: 48px; top: 34px;
    font-size: 30px; font-weight: 400; letter-spacing: 1px;
    color: var(--gold);
  }
  .side-tab {
    position: absolute; left: 0; top: 182px; width: 36px; height: 170px;
    background: var(--gold-soft);
    border-radius: 0 14px 0 0;
  }
  .side-tab .page-number {
    position: absolute; left: 0; bottom: 0; width: 36px; height: 30px;
    background: var(--slate);
    color: #ddd; font-size: 8px; line-height: 30px; text-align: center;
    border-radius: 0 12px 0 0;
  }
  .feature-card {
    position: absolute; left: 50px; top: 100px; width: 300px; height: 240px;
    border-radius: 12px; overflow: hidden; background: var(--gold-soft);
  }
  .feature-photo {
    height: 158px;
    background: linear-gradient(180deg, #6b7480 0%, #aeb4b9 38%, #d8d2c2 62%, #c9b995 100%);
  }
  .feature-icons {
    display: flex; justify-content: space-around; align-items: flex-start;
    padding: 12px 10px 0;
  }
  .feature {
    width: 64px; text-align: center; color: #fff;
    font-size: 7.5px; line-height: 1.2; font-weight: 300;
  }
  .feature svg { display: block; margin: 0 auto 5px; }
  .about-copy {
    position: absolute; left: 368px; top: 100px; width: 168px;
    font-size: 6.8px; line-height: 1.35; color: var(--ink); text-align: justify;
  }
  .about-copy .policy {
    margin-top: 6px; color: var(--gold-text); font-weight: 600;
    text-transform: uppercase; letter-spacing: 0.2px;
  }
  .checklist { list-style: none; margin-top: 8px; }
  .checklist li {
    position: relative; padding-left: 10px; margin-bottom: 6px; text-align: left;
  }
  .checklist li svg { position: absolute; left: 0; top: 1px; }
  .site-footer {
    position: absolute; right: 0; bottom: 0; width: 130px; height: 22px;
    background: var(--footer);
    display: flex; align-items: center; gap: 6px; padding-left: 12px;
    font-size: 6.5px; color: #666;
  }
  .site-footer .mark { width: 8px; height: 8px; border: 1.5px solid var(--ink); }

  /* TABLE OF CONTENT cover */
  .contents-cover {
    left: 30px;
    background: linear-gradient(135deg, var(--charcoal-light) 0%, var(--charcoal) 45%, #262626 100%);
  }
  .contents-panel {
    position: absolute; left: 150px; top: 120px; width: 340px; height: 175px;
    background: linear-gradient(135deg, #f4f4f4 0%, var(--silver) 50%, #d6d6d6 100%);
    border: 4px solid var(--gold);
    border-radius: 16px;
  }
  .contents-label {
    position: absolute; left: 120px; top: 130px; width: 205px; height: 22px;
    background: var(--charcoal);
    color: var(--gold); font-size: 13px; font-weight: 300; letter-spacing: 0.5px;
    line-height: 22px; padding-left: 10px;
  }
  .contents-list {
    position: absolute; left: 205px; top: 165px;
    list-style: none; font-family: "Montserrat", Arial, sans-serif;
    font-weight: 700; font-size: 10.5px; line-height: 12.5px; color: var(--ink);
  }
  .contents-list li span { display: inline-block; width: 26px; font-weight: 600; }
</style>
</head>
<body>

<section class="page about-page">
  <h1 class="about-title">ABOUT US</h1>
  <div class="side-tab"><div class="page-number">2</div></div>

  <div class="feature-card">
    <div class="feature-photo" role="img" aria-label="Photograph of an elephant herd crossing a dry savanna under a cloudy sky"></div>
    <div class="feature-icons">
      <div class="feature">
        <svg width="22" height="26" viewBox="0 0 22 26" fill="none" stroke="#fff" stroke-width="1.2">
          <rect x="2" y="3" width="18" height="22" rx="1.5"/><rect x="7" y="1" width="8" height="4" rx="1"/>
          <line x1="6" y1="10" x2="16" y2="10"/><line x1="6" y1="14" x2="16" y2="14"/><line x1="6" y1="18" x2="16" y2="18"/>
        </svg>Catalogue
      </div>
      <div class="feature">
        <svg width="28" height="26" viewBox="0 0 28 26" fill="none" stroke="#fff" stroke-width="1.2">
          <path d="M14 14 V6"/><path d="M14 9 C10 9 8 6 8 3 C11 3 14 5 14 9"/><path d="M14 8 C18 8 20 5 20 2 C17 2 14 4 14 8"/>
          <path d="M2 18 C6 16 9 16 13 18 L19 18 C21 18 21 21 19 21 L12 21"/><path d="M19 20 L25 16 C27 15 28 17 26 19 L19 24 L2 24"/>
        </svg>Handmade Craftmanship
      </div>
      <div class="feature">
        <svg width="22" height="26" viewBox="0 0 22 26" fill="none" stroke="#fff" stroke-width="1.2">
          <path d="M11 25 C5 17 3 14 3 10 A8 8 0 0 1 19 10 C19 14 17 17 11 25 Z"/>
          <circle cx="11" cy="10" r="4.5"/><line x1="6.5" y1="10" x2="15.5" y2="10"/><ellipse cx="11" cy="10" rx="2" ry="4.5"/>
        </svg>Manufactured in South Africa
      </div>
      <div class="feature">
        <svg width="24" height="26" viewBox="0 0 24 26" fill="none" stroke="#fff" stroke-width="1.2">
          <path d="M4 22 C4 10 12 4 21 4 C21 14 15 22 4 22 Z"/><path d="M4 22 L15 11"/>
        </svg>Sustainable
      </div>
    </div>
  </div>

  <div class="about-copy">
    <p>Our style is contemporary “safari chic” while studiously avoiding any overt tribal / African / village handicraft references. Vostre Merchant Co offers a wide variety of up-market products for the home such as decorative lighting, furniture, accessories, cushions and rugs. Products are handmade, in South Africa, of exotic indigenous materials such as feathers, ostrich eggs, leather, porcupine quills, suede, horns, ostrich shins, and a variety of game skins.</p>
    <p class="policy">We operate a sustainable model of sourcing &amp; manufacturing: all of our products have been sourced from suppliers who are commited to ethical business practices. For clarity, this means that:</p>
    <ul class="checklist">
      <li><svg width="7" height="7" viewBox="0 0 7 7" fill="none" stroke="#2b2b2b" stroke-width="0.8"><rect x="0.4" y="0.4" width="6.2" height="6.2"/><path d="M1.5 3.5 L3 5 L5.8 1.5"/></svg>All animal skulls have been sourced from game reserves where the animal has died in the wild, or been killed during a legislated cull</li>
      <li><svg width="7" height="7" viewBox="0 0 7 7" fill="none" stroke="#2b2b2b" stroke-width="0.8"><rect x="0.4" y="0.4" width="6.2" height="6.2"/><path d="M1.5 3.5 L3 5 L5.8 1.5"/></svg>All cow horns and leather have been sourced from farms whose primary business is raising cattle as a food source, and who sell the cow horns &amp; skins as a by-product of food production</li>
      <li><svg width="7" height="7" viewBox="0 0 7 7" fill="none" stroke="#2b2b2b" stroke-width="0.8"><rect x="0.4" y="0.4" width="6.2" height="6.2"/><path d="M1.5 3.5 L3 5 L5.8 1.5"/></svg>The artisans working in the tanneries and factories in which our products are made are paid a living wage, and who work in a environment that is regularly examined by independent regulators.</li>
    </ul>
  </div>

  <div class="site-footer"><span class="mark"></span>www.vostremerchant.example</div>
</section>

<section class="page contents-cover">
  <div class="contents-panel"></div>
  <div class="contents-label">TABLE OF CONTENT</div>
  <ol class="contents-list">
    <li><span>1.</span>Chandeliers</li>
    <li><span>2.</span>Lamps</li>
    <li><span>3.</span>Furniture</li>
    <li><span>4.</span>Wall Art</li>
    <li><span>5.</span>Hides &amp; Skins</li>
    <li><span>6.</span>Horns &amp; Skulls</li>
    <li><span>7.</span>Decor</li>
    <li><span>8.</span>Lamp Shades</li>
    <li><span>9.</span>Contact Us</li>
  </ol>
</section>

</body>
</html>
```